Construction material supplies company business card ****

1. Full company name “K T Masonry Works Ltd”
I am after a Business card design for the company as a whole. We are better known in Solomon Islands as “K T Masonry” for short.

We are a building materials supplier of
Ready Mixed Concrete, Bricks and Blocks,
Quarry products- gravel, aggregates, sand etc.
Cement distributor/retailer of reputable brands.
Other prefab concrete products. Culverts, wave breakers, concrete retaining blocks etc.

2. Competitive Advantage over Competition: Quality, efficient, professional, dependable, reliable

3. We want people to feel trust worthy, high quality, strong when they see our brand

5. No preference to color. Maybe more sturdy and corporate. Not fancy.

Industry/Entity Type

CONSTRUCTION SUPPLY

Contact Information for Business Card

Name, Position, office phone mob phone, email

Requirements
Must have
• the company logo
Nice to have
• would like to see a mixture of designs, of with logo only and also with simple graphic designs to bring out the company whilst still have the strong sturdy professional feeling

```html
<!DOCTYPE html>
<html lang="en">
<head>
<meta charset="utf-8">
<title>K T Masonry – Business Card</title>
<link href="https://fonts.googleapis.com/css2?family=Roboto:wght@400;500;700&display=swap" rel="stylesheet">
<style>
  :root{
    --page:#2a2a2c;
    --navy:#1b3d63;
    --navy-text:#1e3a5e;
    --concrete:#e6e6e5;
    --concrete-dark:#d2d2d1;
    --curve-edge:#3a3d42;
    --light-text:#eef1f5;
    --white:#ffffff;
  }
  *{box-sizing:border-box;margin:0;padding:0}
  html,body{width:1200px;height:1138px;overflow:hidden;background:var(--page);font-family:"Roboto",Arial,sans-serif}
  .card{
    position:absolute;width:620px;height:374px;border-radius:16px;overflow:hidden;
    background:radial-gradient(ellipse at 40% 35%,#f2f2f1 0%,var(--concrete) 55%,var(--concrete-dark) 100%);
    box-shadow:0 6px 14px rgba(0,0,0,.45);
  }
  .card--front{left:274px;top:186px}
  .card--back{left:276px;top:608px}

  /* front */
  .brand{position:absolute;left:0;right:0;top:70px;display:flex;justify-content:center;align-items:center;gap:18px}
  .brand__mark{width:42px;height:42px;background:var(--navy)}
  .brand__name{font-weight:700;font-size:46px;letter-spacing:1px;color:var(--navy-text);line-height:1}
  .band{position:absolute;left:0;right:0;top:212px;height:80px;background:var(--navy)}
  .pill{
    position:absolute;left:136px;top:185px;width:348px;height:41px;border-radius:21px;
    background:var(--navy);border:2px solid #e8e8e8;
    color:var(--light-text);font-size:16px;display:flex;align-items:center;justify-content:center;
  }
  .band__text{position:absolute;left:0;right:0;top:239px;text-align:center;color:var(--light-text);font-size:16px;line-height:21px}
  .services{position:absolute;left:0;right:0;top:305px;text-align:center;color:var(--navy-text);font-size:16px;line-height:24px}

  /* back */
  .back-art{position:absolute;inset:0}
  .back-brand{position:absolute;left:20px;width:262px;top:150px;display:flex;flex-direction:column;align-items:center;gap:22px}
  .back-brand__mark{width:54px;height:54px;background:var(--white)}
  .back-brand__name{font-weight:700;font-size:30px;letter-spacing:1px;color:var(--white);line-height:1}
  .person{position:absolute;left:349px;top:62px;color:var(--navy-text)}
  .person__name{font-weight:700;font-size:23px;line-height:28px}
  .person__role{font-size:17px;line-height:22px;color:#2c4668}
  .contacts{position:absolute;left:357px;top:143px;list-style:none;color:var(--navy-text);font-size:17px}
  .contacts li{display:flex;align-items:center;height:25.5px}
  .contacts svg{width:14px;height:14px;margin-right:15px;flex:none}
  .address{position:absolute;left:349px;top:224px;color:#2c4668;font-size:17px;line-height:26px}
  .tagline{position:absolute;left:268px;top:326px;color:var(--light-text);font-size:17px;line-height:22px}
</style>
</head>
<body>

<section class="card card--front">
  <div class="brand">
    <span class="brand__mark"></span>
    <span class="brand__name">K T MASONRY</span>
  </div>
  <div class="band"></div>
  <div class="pill">We are a building materials supplier of</div>
  <p class="band__text">Ready Mixed Concrete, Bricks and Blocks, Quarry Products<br>Quarry Products:- Gravel, Aggregates, Sand Etc.</p>
  <p class="services">Cement Distributor/Retailer of Reputable Brands.<br>Other Concrete Products Culverts, Wave Breakers, Concrete Retaining Blocks</p>
</section>

<section class="card card--back">
  <svg class="back-art" width="620" height="374" viewBox="0 0 620 374">
    <path d="M240 318 H620 V356 H228 Z" fill="var(--navy)"/>
    <path d="M0 0 H272 Q340 180 252 374 H0 Z" fill="var(--curve-edge)"/>
    <path d="M0 0 H256 Q322 180 236 374 H0 Z" fill="var(--navy)"/>
  </svg>
  <div class="back-brand">
    <span class="back-brand__mark"></span>
    <span class="back-brand__name">K T MASONRY</span>
  </div>

  <div class="person">
    <p class="person__name">Daniel Harlow</p>
    <p class="person__role">Managing Director</p>
  </div>

  <ul class="contacts">
    <li>
      <svg viewBox="0 0 16 16"><path fill="var(--navy-text)" d="M2 6c0-2 2.5-3 6-3s6 1 6 3v1h-3.5V5.6h-5V7H2zM4 8h8l2 5H2z"/></svg>
      000 0000 0000
    </li>
    <li>
      <svg viewBox="0 0 16 16"><rect x="1" y="3" width="14" height="10" fill="var(--navy-text)"/><path d="M1.5 3.5 8 9l6.5-5.5" stroke="#eee" stroke-width="1.4" fill="none"/></svg>
      daniel@ktmasonry.com
    </li>
    <li>
      <svg viewBox="0 0 16 16"><circle cx="8" cy="8" r="6.5" fill="var(--navy-text)"/><path d="M1.5 8h13M8 1.5v13M3 4.5h10M3 11.5h10" stroke="#eee" stroke-width=".9"/><ellipse cx="8" cy="8" rx="3" ry="6.5" stroke="#eee" stroke-width=".9" fill="none"/></svg>
      www.ktmasonry.com
    </li>
  </ul>

  <p class="address">18 Harbour Rd., Point Cruz,<br>Honiara, SB 00100</p>

  <p class="tagline">Efficient, Professional, Dependable, Reliable</p>
</section>

</body>
</html>
```